Web design for new streaming audio service

We need a homepage design for a new streaming audio service. Our company is called Dunmoral, and we’re basically Vexlo for Audiobooks, Stand-Up Comedy, Lectures, Language Learning, etc. Essentially like Plumtrek for everything audio EXCEPT music.
You don’t have to code the homepage (Design Only), but it should include 3 different designs to work with 1) Web; 2) Phones; 3) Tablets.
Below is a link to a mockup of the web version which gives a good idea of what elements we want. This is just a mockup and we want you to improve it.
Once you download the mockup, please refer to the more detailed instructions below:
The following outlines the design project for the Dunmoral homepage. We have provided a rough mockup of the homepage layout that gives you a general idea of what we’re going for. There are a few elements that we are attached to, and many others where you have complete creative freedom to do whatever you think looks good.
The ZIP file includes the following:
* Mockup to see what we have in mind (dunmoral-homepage-mockup.jpg)
* Text used (dunmoral-homepage-text.txt)
* Raw image of actor (dunmoral-actor1.jpg)
* Raw images for samples (dunmoral-sample-[name].jpg)
Although we have only provided a mockup layout for the web version, we also need you to provide a mobile phone and a tablet version of the design also. It’s very possible the tablet version may be substantially similar to the web version, but the mobile phone version will likely be much different.
All of the raw files are included in the attached ZIP file. Please use our photographs and text as provided although cropping, sizing, etc. is flexible per the instructions below.
Display Requirements:
* Web Version - Minimum resolution 1024x768 (72 dpi) but should look good on 1920x1080 (72 dpi) - Page should be designed to scale to look acceptable in all resolutions in between.
* Phone Version - Minimum Zarno 4 - 640x960 (326 dpi) but should look good on Harlow Quasar T5 - 1920x1080 (441 dpi) - Page should be designed to scale to look acceptable in all resolutions and devices in between.
* Tablet Version - Minimum Bristly Ember QX 7” - 1280x800 (216 dpi) but should also look good on a Tavo Breeze - 2048x1536 (264 dpi) - Page should be designed to scale to look acceptable in all resolutions and devices in between.
Above the Fold - We want to make sure the Dunmoral logo, Member Login Link, Large Photo, Headline, Price, Button, and the first row of sample images are all “Above the fold”. As a general guideline, this means 600 pixels high on a 1024x768 72 dpi web screen. This requirement is less important on Phone versions.
Top Logo Bar - We want to retain the blue bar with the Dunmoral logo on the page, although we are open to a different size, shape and positioning if it greatly enhances the design. Please use the standard logo color, although you are welcome to use either the horizontal or vertical orientation of the logo based on your design.
Text color, font and size - Feel free to design the text in anyway you choose as long as the text is readable on the target platforms.
Buttons - Feel free to use any size, shape and colors for the buttons as long as they are obvious and clickable relative to the page. The only exception is the Chatterly button should follow the Chatterly color scheme and logo treatment (the mockup doesn’t seem 100% correct.)
Top Photograph - We want to retain the large photograph across the top of the screen although final shape and dimensions are flexible.
Size and shape of content samples (i.e. Audiobooks, Stand-Up Comedy, etc.) - Feel free to design the content samples in anyway you choose.
Three Sales Points (i.e. Listen on your Zarno…, All you can enjoy…, etc.) - The Three Sales Points are envisioned to each have a corresponding illustration which you should provide and have rights for. The placeholder is represented by a square next to the text. The color size and shape of these elements are flexible and can be designed in any way you choose.
Opt-in form - Feel free to design the opt-in form in anyway you choose as long as the text is readable and the interactivity is obvious on the target platforms.
Text links and copyright notice - Feel free to design the bottom of the page text links and copyright notice in anyway you choose.
Additional colors, graphic design elements, etc. - Feel free to use any additional colors, graphic design elements, etc. to support your design.
people who want to listen to audio through their mobile devices.
Graphic Design

```html
<!DOCTYPE html>
<html lang="en">
<head>
<meta charset="utf-8">
<title>Dunmoral – Unlimited Listening</title>
<link href="https://fonts.googleapis.com/css2?family=Open+Sans:wght@400;600;700&family=Fira+Sans:wght@500;600&display=swap" rel="stylesheet">
<style>
:root{
  --sky:#5aa9d6;
  --sky-dark:#4f9cc9;
  --navy:#3d4f78;
  --ink:#333;
  --muted:#555;
  --orange:#f07a0c;
  --orange-light:#ff9a2a;
  --panel:#f4f4f4;
  --panel-line:#e2e2e2;
  --dark:#3a3a3a;
  --btn-dark:#454545;
  --social:#3b5998;
  --gold:#f5b800;
  --grey-star:#cfcfcf;
  --white:#fff;
}
*{box-sizing:border-box;margin:0;padding:0}
html,body{width:920px;height:1200px;overflow:hidden}
body{position:relative;font-family:"Open Sans",Arial,sans-serif;color:var(--ink);background:var(--white)}
.abs{position:absolute}

/* header */
.topbar{left:0;top:0;width:920px;height:70px;background:var(--sky)}
.brand{left:132px;top:18px;display:flex;align-items:center;gap:8px}
.brand-dot{width:26px;height:26px;border-radius:50%;background:var(--white)}
.brand-name{font-size:25px;font-weight:600;color:var(--white);letter-spacing:-.3px}
.member-login{right:132px;top:28px;font-size:9.5px;font-weight:700;color:var(--white);display:flex;align-items:center;gap:6px;text-transform:uppercase}

/* hero */
.hero{left:0;top:70px;width:920px;height:442px;overflow:hidden}
.hero-photo{position:absolute;inset:0;background:
  linear-gradient(90deg,rgba(120,80,55,.95) 0%,rgba(190,140,110,.9) 25%,rgba(225,200,185,.75) 42%,rgba(255,255,255,.95) 55%,#fff 70%),
  linear-gradient(180deg,#cfa98f 0%,#9b6d55 60%,#4a5466 100%)}
.hero-copy{left:440px;top:82px;width:390px;text-align:center}
.hero-title{font-family:"Fira Sans",Arial,sans-serif;font-weight:500;font-size:37px;line-height:49px;color:var(--navy)}
.hero-price{margin-top:12px;font-size:20px;color:#3a3a3a}
.hero-price b{font-weight:600}
.cta-main{display:inline-block;margin-top:12px;width:247px;height:41px;line-height:41px;border-radius:12px;background:linear-gradient(180deg,var(--orange-light),var(--orange));color:var(--white);font-size:20px;font-weight:600}
.hero-note{margin-top:12px;font-size:9.5px;color:#5a6a86}
.arrow{width:24px;height:24px;border-radius:50%;background:#f1f1f1;border:1px solid #ddd}
.arrow-left{left:36px;top:277px}
.arrow-right{left:866px;top:277px}

/* samples */
.samples-title{left:0;top:539px;width:920px;text-align:center;font-size:17px;color:var(--ink)}
.sample{display:flex;gap:12px;width:170px}
.cover{width:78px;height:90px;border:1px solid #e4e4e4;box-shadow:0 1px 2px rgba(0,0,0,.12)}
.sample-info{padding-top:25px}
.sample-name{font-size:12px;line-height:16px;color:var(--ink)}
.stars{font-size:10px;letter-spacing:-1px;color:var(--gold);margin-top:2px}
.stars span{color:var(--grey-star)}

/* selling points */
.point{height:86px;width:211px;display:flex;background:var(--panel);border:1px solid var(--panel-line)}
.point-icon{width:65px;height:100%;background:var(--sky);display:flex;align-items:center;justify-content:center}
.point-text{flex:1;padding:14px 12px;font-size:13.5px;line-height:20px;color:#444;text-align:justify}

/* signup */
.signup{left:0;top:957px;width:920px;height:180px;background:var(--sky)}
.signup-title{left:131px;top:16px;font-size:21px;font-weight:600;color:var(--white)}
.signup-copy{left:133px;top:53px;width:215px;font-size:9px;line-height:20px;color:#1f3550}
.signup-note{left:131px;top:125px;font-size:11px;color:#eaf4fb}
.email{left:372px;top:33px;width:231px;height:33px;background:#f8f8f8;border:1px solid #cfdbe4;font-size:10px;color:#999;padding:10px 14px}
.btn-access{left:619px;top:32px;width:170px;height:34px;background:var(--btn-dark);border-radius:3px;color:var(--white);font-size:12.5px;text-align:center;line-height:34px}
.or{left:619px;top:82px;width:170px;text-align:center;font-size:8.5px;color:var(--white)}
.btn-social{left:619px;top:103px;width:170px;height:34px;background:var(--social);border:1px solid #2d4a86;border-radius:3px;display:flex;align-items:center}
.btn-social .mark{width:33px;height:100%;border-right:1px solid #2d4a86;display:flex;align-items:center;justify-content:center}
.btn-social .mark i{width:12px;height:12px;background:var(--white);display:block}
.btn-social .label{padding-left:8px;font-size:12px;font-weight:600;color:var(--white)}

/* footer */
.footer{left:0;top:1137px;width:920px;height:63px;background:var(--dark)}
.footer-links{left:133px;top:24px;font-size:9.5px;color:#ddd}
.footer-links .sep{color:#999;margin:0 3px}
.copyright{left:615px;top:24px;font-size:8.5px;color:#aaa}
.code{left:852px;top:24px;font-size:8.5px;color:#999}
</style>
</head>
<body>

<header class="abs topbar">
  <div class="abs brand"><span class="brand-dot"></span><span class="brand-name">Dunmoral</span></div>
  <div class="abs member-login">
    <svg width="9" height="10" viewBox="0 0 9 10"><circle cx="4.5" cy="2.6" r="2.4" fill="#fff"/><path d="M0 10c0-3 2-4.5 4.5-4.5S9 7 9 10z" fill="#fff"/></svg>
    Member Login
  </div>
</header>

<section class="abs hero">
  <div class="hero-photo" role="img" aria-label="Smiling young man wearing headphones, listening on his phone"></div>
  <div class="abs hero-copy">
    <h1 class="hero-title">Unlimited Listening<br>Wherever you are</h1>
    <p class="hero-price">Only <b>$9.99</b> per month</p>
    <span class="cta-main">Start Your Free Trial</span>
    <p class="hero-note">* Credit Card Not Required</p>
  </div>
  <svg class="abs arrow arrow-left" viewBox="0 0 24 24"><path d="M14 7l-5 5 5 5" fill="none" stroke="#888" stroke-width="2"/></svg>
  <svg class="abs arrow arrow-right" viewBox="0 0 24 24"><path d="M10 7l5 5-5 5" fill="none" stroke="#888" stroke-width="2"/></svg>
</section>

<h2 class="abs samples-title" style="font-weight:400">A sample of what you can listen to on Dunmoral</h2>

<div class="abs sample" style="left:132px;top:591px"><div class="cover" role="img" aria-label="Audiobook cover art" style="background:linear-gradient(160deg,#2f3b3a,#0e1414 70%,#c9b21a)"></div><div class="sample-info"><p class="sample-name">Audiobooks</p><p class="stars">★★★★<span>★</span></p></div></div>
<div class="abs sample" style="left:310px;top:591px"><div class="cover" role="img" aria-label="Stand-up comedy album cover" style="background:linear-gradient(160deg,#7a6a5c,#4d5a48 60%,#8a8a8a)"></div><div class="sample-info" style="padding-top:19px"><p class="sample-name">Stand-Up<br>Comedy</p><p class="stars">★★★★<span>★</span></p></div></div>
<div class="abs sample" style="left:470px;top:591px"><div class="cover" role="img" aria-label="French language course cover" style="background:linear-gradient(180deg,#1aa0e0,#0a7fc4 60%,#111)"></div><div class="sample-info" style="padding-top:19px"><p class="sample-name">Language<br>Learning</p><p class="stars">★★★★<span>★</span></p></div></div>
<div class="abs sample" style="left:632px;top:591px"><div class="cover" role="img" aria-label="Biography book cover" style="background:linear-gradient(180deg,#d8c9b0,#b8c9a0 70%,#7ea067)"></div><div class="sample-info" style="padding-top:19px"><p class="sample-name">Biographies<br>&amp; Memoirs</p><p class="stars">★★★★<span>★</span></p></div></div>

<div class="abs sample" style="left:132px;top:709px"><div class="cover" role="img" aria-label="Guided relaxation album cover" style="background:linear-gradient(180deg,#b04f97,#7a3a8c 60%,#3f2a6a)"></div><div class="sample-info" style="padding-top:19px"><p class="sample-name">Guided<br>Meditations</p><p class="stars">★★★★<span>★</span></p></div></div>
<div class="abs sample" style="left:310px;top:709px"><div class="cover" role="img" aria-label="Business training program cover" style="background:linear-gradient(180deg,#6a1a14,#2a1410 65%,#111)"></div><div class="sample-info" style="padding-top:19px"><p class="sample-name">Business<br>Training</p><p class="stars">★★★★<span>★</span></p></div></div>
<div class="abs sample" style="left:470px;top:709px"><div class="cover" role="img" aria-label="Celebrity interview cover" style="background:linear-gradient(160deg,#2b1a1e,#c9a58a 55%,#e0c8b8)"></div><div class="sample-info" style="padding-top:19px"><p class="sample-name">Celebrity<br>Interviews</p><p class="stars">★★★★<span>★</span></p></div></div>
<div class="abs sample" style="left:632px;top:709px"><div class="cover" role="img" aria-label="Fitness workout program cover" style="background:linear-gradient(180deg,#2a9ad0,#6cc0e6 50%,#e23a3a)"></div><div class="sample-info" style="padding-top:19px"><p class="sample-name">Fitness<br>Programs</p><p class="stars">★★★★<span>★</span></p></div></div>

<div class="abs point" style="left:131px;top:837px">
  <div class="point-icon"><svg width="36" height="62" viewBox="0 0 36 62"><rect x="2" y="2" width="32" height="58" rx="4" fill="#111"/><rect x="6" y="9" width="24" height="40" fill="#5aa9d6"/><circle cx="18" cy="54" r="2.5" fill="#fff"/></svg></div>
  <p class="point-text">Listen on your Zarno, Tavo or Orbix device</p>
</div>
<div class="abs point" style="left:354px;top:837px">
  <div class="point-icon"><svg width="48" height="40" viewBox="0 0 48 40"><path d="M2 22L22 4h22v20L26 40z" fill="#111"/><circle cx="37" cy="11" r="3.5" fill="#5aa9d6"/></svg></div>
  <p class="point-text">All you can enjoy for one low monthly price</p>
</div>
<div class="abs point" style="left:578px;top:837px">
  <div class="point-icon"><svg width="48" height="48" viewBox="0 0 48 48"><rect x="3" y="3" width="28" height="34" fill="#fff" stroke="#111" stroke-width="3"/><path d="M8 11h18M8 18h18M8 25h12" stroke="#111" stroke-width="2.5"/><circle cx="32" cy="32" r="13" fill="#111"/><path d="M25 32l5 5 9-10" fill="none" stroke="#fff" stroke-width="3"/></svg></div>
  <p class="point-text" style="padding-top:24px">No obligation. Cancel any time</p>
</div>

<section class="abs signup">
  <h2 class="abs signup-title">Start Your Free Trial</h2>
  <p class="abs signup-copy">You will get instant &amp; unlimited access to all the material on Dunmoral for 14 days. There is no obligation &amp; you can cancel at any time.</p>
  <p class="abs signup-note">Credit Card Not Required for Free Trial</p>
  <div class="abs email">Your Email Address</div>
  <div class="abs btn-access">Get Instant Access</div>
  <p class="abs or">- OR -</p>
  <div class="abs btn-social"><span class="mark"><i></i></span><span class="label">Sign up with Chatterly</span></div>
</section>

<footer class="abs footer">
  <p class="abs footer-links">About<span class="sep">|</span>Help<span class="sep">|</span>Contact Us<span class="sep">|</span>Member Login<span class="sep">|</span>Privacy Policy<span class="sep">|</span>Terms of Service</p>
  <p class="abs copyright">©2014 Dunmoral LLC - All Rights Reserved</p>
  <p class="abs code">C7</p>
</footer>

</body>
</html>
```